I need a sophisticated and powerful book cover design that combines Japanese minimalism with contemporary appeal. The cover should convey personal transformation through the metaphor of a katana (Japanese sword).
Key Design Elements:
A katana, either partially shown or artistically rendered
Subtle Japanese design elements without being stereotypical
Clean, minimalist aesthetic
Professional font selection that bridges Eastern and Western typography
Color scheme: Deep blacks, steel grays, and possibly a touch of red or gold for accent
Mood/Style:
Professional and sophisticated
Blend of traditional Japanese aesthetics with modern design
Should appeal to personal development and business readers
Must convey strength and transformation
Elegant rather than aggressive
Specific Requirements:
Title: "The Lantern Compass"
Subtitle: "Quiet Methods for Growing Inner Steadiness and Calm Endurance"
Author names: Dorvelan Thaske and Meloda Thaske
Cover dimensions: Standard hardcover book size (6" x 9")
Must work well in both physical and digital thumbnail formats
Should be striking and legible when viewed as a small image online
Design Specifics:
Japanese elements such as brushstroke effects, kanji characters, or wave patterns
The design should reflect the book's core message: personal transformation through Japanese wisdom principles, using the katana as a metaphor for growth and development.

```html
<!DOCTYPE html>
<html lang="en">
<head>
<meta charset="utf-8">
<title>The Lantern Compass — Book Cover</title>
<link href="https://fonts.googleapis.com/css2?family=Montserrat:wght@400;500;600;900&family=Permanent+Marker&display=swap" rel="stylesheet">
<style>
  :root {
    --stage: #000000;
    --cream: #f3e8dd;
    --cream-light: #f7ede2;
    --blush: #f4cfc3;
    --sun-red: #e8352b;
    --steel: #c9c4c4;
    --accent-red: #ed1c24;
    --ink: #111111;
    --paper-white: #ffffff;
  }
  * { margin: 0; padding: 0; box-sizing: border-box; }
  html, body {
    width: 1200px;
    height: 1200px;
    overflow: hidden;
    background: var(--stage);
  }
  .stage {
    position: relative;
    width: 1200px;
    height: 1200px;
    background: var(--stage);
  }
  .cover {
    position: absolute;
    left: 240px;
    top: 60px;
    width: 720px;
    height: 1080px;
    background: var(--cream);
    overflow: hidden;
  }
  .cover-art {
    position: absolute;
    left: 0;
    top: 0;
    width: 720px;
    height: 620px;
    background:
      linear-gradient(180deg,
        rgba(243,232,221,0) 0%,
        rgba(243,232,221,0) 68%,
        var(--cream) 100%),
      linear-gradient(180deg,
        rgba(201,196,196,0) 200px,
        rgba(201,196,196,0.55) 240px,
        rgba(232,53,43,0.35) 280px,
        rgba(201,196,196,0.55) 330px,
        rgba(201,196,196,0.45) 380px,
        rgba(201,196,196,0) 420px),
      radial-gradient(circle at 362px 235px, var(--sun-red) 0 138px, rgba(232,53,43,0) 146px),
      radial-gradient(ellipse 420px 220px at 50% 420px, var(--blush) 0%, rgba(244,207,195,0) 100%),
      linear-gradient(180deg, var(--cream-light) 0%, #f5e2d8 60%, var(--cream) 100%);
  }
  .title {
    position: absolute;
    left: 0;
    top: 0;
    width: 720px;
    height: 560px;
    font-weight: normal;
  }
  .title span {
    position: absolute;
    left: 0;
    width: 720px;
    text-align: center;
    white-space: nowrap;
  }
  .title-lead {
    top: 472px;
    font-family: "Montserrat", sans-serif;
    font-weight: 900;
    font-size: 92px;
    line-height: 92px;
    letter-spacing: 7px;
    color: var(--ink);
  }
  .title-brush {
    top: 548px;
    font-family: "Permanent Marker", cursive;
    font-size: 122px;
    line-height: 140px;
    color: var(--accent-red);
  }
  .title-main {
    top: 672px;
    font-family: "Montserrat", sans-serif;
    font-weight: 600;
    font-size: 120px;
    line-height: 130px;
    letter-spacing: 2px;
    color: var(--accent-red);
  }
  .subtitle {
    position: absolute;
    left: 40px;
    top: 810px;
    width: 640px;
    text-align: center;
    font-family: "Montserrat", sans-serif;
    font-weight: 500;
    font-size: 31px;
    line-height: 44px;
    color: var(--ink);
  }
  .author-band {
    position: absolute;
    left: 0;
    bottom: 0;
    width: 720px;
    height: 115px;
    background: var(--accent-red);
    display: flex;
    align-items: center;
    justify-content: center;
  }
  .author-names {
    font-family: "Montserrat", sans-serif;
    font-weight: 500;
    font-size: 36px;
    color: var(--paper-white);
    white-space: nowrap;
  }
</style>
</head>
<body>
  <main class="stage">
    <section class="cover">
      <div class="cover-art" role="img" aria-label="Illustration: three katanas laid horizontally across a red rising sun, with a cherry blossom branch, falling petals and soft pink clouds"></div>

      <h1 class="title">
        <span class="title-lead">THE</span>
        <span class="title-brush">LANTERN</span>
        <span class="title-main">COMPASS</span>
      </h1>

      <p class="subtitle">Quiet Methods for Growing Inner Steadiness and Calm Endurance</p>

      <footer class="author-band">
        <p class="author-names">Dorvelan Thaske &amp; Meloda Thaske</p>
      </footer>
    </section>
  </main>
</body>
</html>
```